Harrow Grading LLC business card design

Excavation company business cards

Contact Information for Business Card

Harrow Grading LLC cell phone 208-417-6290 office phone 208-319-4856 harrowgradingllc@maplecove.com Driveways, site prep, retaining walls, septic systems, rock delivery

Colors

Designer to choose colors to be used in the design.

```html
<!DOCTYPE html>
<html lang="en">
<head>
<meta charset="utf-8">
<title>Harrow Grading LLC – Business Card</title>
<link rel="stylesheet" href="https://fonts.googleapis.com/css2?family=Orbitron:wght@700;800&family=Rubik:wght@400;500&display=swap">
<style>
  :root {
    --orange: #ec7424;
    --ink: #1d1d1d;
    --grey-text: #555555;
    --rule: #9a9a9a;
    --band: #6a6a6a;
    --card-back-top: #7b7b7b;
    --card-back-bottom: #646464;
    --page: #e4e4e4;
    --white: #ffffff;
  }
  html, body {
    margin: 0;
    width: 1200px;
    height: 1200px;
    overflow: hidden;
    background: var(--page);
  }
  .stage {
    position: relative;
    width: 1400px;
    height: 1400px;
    transform: scale(0.857143);
    transform-origin: 0 0;
  }
  .card {
    position: absolute;
    left: 306px;
    width: 800px;
    height: 457px;
    overflow: hidden;
    box-shadow: 0 18px 28px rgba(0,0,0,0.18);
  }
  .card--front { top: 193px; background: var(--white); }
  .card--back {
    top: 762px;
    background: linear-gradient(180deg, var(--card-back-top), var(--card-back-bottom));
  }

  .brand-name {
    position: absolute;
    right: 51px;
    top: 135px;
    margin: 0;
    font-family: "Orbitron", sans-serif;
    font-weight: 800;
    font-size: 21px;
    letter-spacing: 0.02em;
    color: var(--orange);
    white-space: nowrap;
  }

  .person { position: absolute; left: 48px; top: 260px; }
  .person__name {
    margin: 0;
    font-family: "Orbitron", sans-serif;
    font-weight: 800;
    font-size: 22px;
    letter-spacing: 0.02em;
    color: var(--orange);
    line-height: 1;
  }
  .person__title {
    margin: 9px 0 0;
    font-family: "Rubik", sans-serif;
    font-size: 16px;
    color: var(--grey-text);
    letter-spacing: 0.04em;
  }
  .divider {
    position: absolute;
    left: 48px;
    top: 320px;
    width: 698px;
    height: 1px;
    background: var(--rule);
  }
  .contacts {
    position: absolute;
    left: 46px;
    top: 333px;
    margin: 0;
    padding: 0;
    list-style: none;
    font-family: "Rubik", sans-serif;
    font-size: 17px;
    color: var(--ink);
  }
  .contacts li {
    display: flex;
    align-items: center;
    gap: 9px;
    height: 23px;
  }
  .contacts svg { width: 14px; height: 14px; fill: var(--orange); flex: none; }

  .footer-band {
    position: absolute;
    left: 0;
    bottom: 0;
    width: 800px;
    height: 36px;
  }
  .footer-url {
    position: absolute;
    right: 0;
    bottom: 17px;
    width: 285px;
    text-align: center;
    font-family: "Rubik", sans-serif;
    font-weight: 500;
    font-size: 17px;
    color: var(--white);
    line-height: 1;
  }

  .back-name {
    position: absolute;
    left: 0;
    right: 0;
    top: 180px;
    margin: 0;
    text-align: center;
    font-family: "Orbitron", sans-serif;
    font-weight: 800;
    font-size: 40px;
    letter-spacing: 0.03em;
    color: #3c3c3c;
  }
  .back-url {
    position: absolute;
    left: 0;
    right: 0;
    top: 402px;
    margin: 0;
    text-align: center;
    font-family: "Rubik", sans-serif;
    font-weight: 500;
    font-size: 16px;
    letter-spacing: 0.5em;
    color: var(--white);
  }
</style>
</head>
<body>
<div class="stage">

  <section class="card card--front">
    <p class="brand-name">HARROW GRADING LLC</p>

    <div class="person">
      <h1 class="person__name">DANIEL REYES</h1>
      <p class="person__title">President</p>
    </div>
    <div class="divider"></div>

    <ul class="contacts">
      <li>
        <svg viewBox="0 0 24 24" aria-hidden="true"><path d="M6.6 10.8a15.1 15.1 0 0 0 6.6 6.6l2.2-2.2a1 1 0 0 1 1-.25 11.4 11.4 0 0 0 3.6.57 1 1 0 0 1 1 1V20a1 1 0 0 1-1 1A17 17 0 0 1 3 4a1 1 0 0 1 1-1h3.5a1 1 0 0 1 1 1c0 1.25.2 2.45.57 3.57a1 1 0 0 1-.25 1z"/></svg>
        208-319-4856
      </li>
      <li>
        <svg viewBox="0 0 24 24" aria-hidden="true"><path d="M7 1h10a2 2 0 0 1 2 2v18a2 2 0 0 1-2 2H7a2 2 0 0 1-2-2V3a2 2 0 0 1 2-2zm0 3v14h10V4z"/></svg>
        208-417-6290
      </li>
      <li>
        <svg viewBox="0 0 24 24" aria-hidden="true"><path d="M2 5h20v14H2zm2 2v.5l8 5 8-5V7l-8 5z"/></svg>
        harrowgradingllc@maplecove.com
      </li>
    </ul>

    <svg class="footer-band" viewBox="0 0 800 36" aria-hidden="true">
      <rect x="0" y="19" width="800" height="17" fill="var(--band)"/>
      <polygon points="8,36 17,20 22,20 13,36" fill="var(--white)"/>
      <polygon points="22,36 31,20 36,20 27,36" fill="var(--white)"/>
      <polygon points="36,36 45,20 50,20 41,36" fill="var(--white)"/>
      <polygon points="492,36 513,0 800,0 800,36" fill="var(--white)"/>
      <polygon points="500,36 521,0 800,0 800,36" fill="var(--orange)"/>
    </svg>
    <div class="footer-url">harrowgradingllc.com</div>
  </section>

  <section class="card card--back">
    <p class="back-name">HARROW GRADING LLC</p>
    <p class="back-url">WWW.HARROWGRADINGLLC.COM</p>
  </section>

</div>
</body>
</html>
```